Onboarding Infographic/brochure

We are a small criminal defense firm looking to create some sort of infographic or brochure that we can onboard new clients with. We are currently sending it out via email but want something a bit cooler and fun to send to clients. The information is:

A Few Quick Rules

We are here to help each step of the way. While questions are never discouraged, this letter will answer some of the most common ones we get asked.

Communications

As a client, you should always be in the loop. While we will try to respond to questions as quickly as possible, sometimes we are unable to respond right away. Do not worry - we promise to get back to you soon. Some questions might take some time to research, and a correct answer is better than a quick one.

Appointments

One of the benefits of having an attorney is the ability to discuss your case outside of court, minus the stress and headaches. If you need an appointment, please contact the office.

Appointments must be scheduled in advance. We do not want you to make a special trip to the office only to learn that we are in court or otherwise unavailable.

Jail Visits

If your family member is currently in jail, we take that very seriously. We will visit your loved one and introduce ourselves. While the case is ongoing, we ask that a family member be designated a “contact” person so that messages can be relayed quickly. Never discuss the facts of the case over the phone with someone who is in jail. Jail calls are recorded and we have seen too many cases go south based on remarks made over recorded lines.

Police Reports and Discovery

We will do our best to provide you with copies of everything we receive on your case. Most information will be emailed, so please keep your email address up to date.

Changes in Contact Information

If you move or change numbers during the case, please let us know. It is difficult to help if we are unable to reach you, and helping you is why we are here.

Court Appearances

Cases do not get resolved as quickly as they do on television. Expect there to be several hearings in your case and it may be necessary for you to attend one or more of them. If a hearing is set, you will receive notice of the date and time of each hearing.

Billing and Collections

We understand that this investment was a huge decision for you. As we focus on providing the best representation, we will need for you to stay on schedule with any payment arrangements agreed to at the time of your initial consultation.

Again, thank you for your trust in us. We look forward to getting a fantastic outcome on your case.

Target Market(s)

Criminal defense clients and their families

Industry/Entity Type

Legal

Font styles to use
Serif

Requirements
Must have
• Must incorporate all of the rules we email out. Would like diagrams, images or pictures
Nice to have
• We attached a Welcome brochure. Not sure I want it to look super similar, hence the request for infographic.

```html
<!DOCTYPE html>
<html lang="en">
<head>
<meta charset="utf-8">
<title>A Few Quick Rules – Meridian Legal Group</title>
<link href="https://fonts.googleapis.com/css2?family=Montserrat:wght@400;600;700&display=swap" rel="stylesheet">
<style>
  :root{
    --blue:#0a3aff;
    --ink:#1b1b22;
    --panel:#f4f4fa;
    --band:#d3d3d6;
    --dot:#c9c9d2;
    --white:#ffffff;
    --tint-a:#dfe6ff;
    --tint-b:#c4d1ff;
  }
  html,body{margin:0;padding:0;overflow:hidden;background:var(--white);}
  .sheet{position:relative;width:1200px;height:980px;overflow:hidden;background:var(--white);font-family:"Montserrat",Arial,sans-serif;color:var(--ink);}
  .intro-band{position:absolute;left:36px;top:36px;width:1128px;height:71px;background:var(--band);}
  .intro-text{position:absolute;left:30px;top:15px;margin:0;font-size:16.5px;font-weight:700;line-height:19.5px;color:var(--ink);}
  .firm-name{position:absolute;right:30px;top:22px;display:flex;align-items:center;gap:9px;font-size:20.5px;font-weight:600;letter-spacing:.2px;color:var(--ink);}
  .firm-mark{width:12px;height:12px;background:var(--blue);}
  .rules-field{position:absolute;left:36px;top:129px;width:1128px;height:751px;background:var(--panel);}
  .dividers{position:absolute;left:0;top:0;}
  .rule{position:absolute;}
  .rule h2{margin:0 0 24px;font-size:17px;font-weight:700;line-height:20px;color:var(--blue);white-space:nowrap;}
  .rule p{margin:0 0 15.9px;font-size:13.8px;line-height:15.9px;font-weight:400;white-space:nowrap;}
  .rule-communications{left:66px;top:157px;}
  .rule-appointments{left:641px;top:157px;}
  .rule-jail{left:66px;top:392px;}
  .rule-discovery{left:792px;top:440px;}
  .rule-contact{left:66px;top:709px;}
  .rule-court{left:400px;top:709px;width:400px;text-align:center;}
  .rule-billing{left:782px;top:709px;width:350px;text-align:right;}
  .hub-art{position:absolute;left:568px;top:465px;width:64px;height:52px;border-radius:4px;background:linear-gradient(135deg,var(--tint-a),var(--tint-b));}
  .hub-title{position:absolute;left:500px;top:522px;width:200px;text-align:center;margin:0;font-size:16.5px;font-weight:700;line-height:19px;color:var(--blue);}
  .closing-band{position:absolute;left:36px;top:903px;width:1128px;height:41px;background:var(--blue);display:flex;align-items:center;justify-content:center;}
  .closing-band p{margin:0;color:var(--white);font-size:16.5px;font-weight:700;}
</style>
</head>
<body>
<div class="sheet">
  <header class="intro-band">
    <p class="intro-text">We are here to help each step of the way. While questions are never discouraged,<br>this letter will answer some of the most common ones we get asked.</p>
    <div class="firm-name"><span class="firm-mark"></span>MERIDIAN LEGAL GROUP</div>
  </header>

  <div class="rules-field"></div>

  <svg class="dividers" width="1200" height="980" viewBox="0 0 1200 980" aria-hidden="true">
    <g fill="none" stroke="var(--white)" stroke-width="22" stroke-linejoin="miter">
      <path d="M600 129V390"/>
      <path d="M30 354H339L491 440"/>
      <path d="M1170 354H861L708 440"/>
      <path d="M30 635H373L480 562"/>
      <path d="M1170 635H827L722 562"/>
      <path d="M353 886L536 627"/>
      <path d="M847 886L666 627"/>
    </g>
    <g fill="none" stroke="var(--dot)" stroke-width="4" stroke-linecap="round" stroke-dasharray="0 14.5">
      <path d="M600 129V390"/>
      <path d="M36 354H339L491 440"/>
      <path d="M1164 354H861L708 440"/>
      <path d="M36 635H373L480 562"/>
      <path d="M1164 635H827L722 562"/>
      <path d="M353 880L536 627"/>
      <path d="M847 880L666 627"/>
    </g>
    <circle cx="600" cy="515" r="131" fill="var(--white)"/>
    <circle cx="600" cy="515" r="88" fill="none" stroke="var(--blue)" stroke-width="14"
      stroke-dasharray="82 10.2" transform="rotate(-87 600 515)"/>

    <g fill="var(--white)" stroke="var(--blue)" stroke-width="1.6">
      <circle cx="541" cy="398" r="21.5"/>
      <circle cx="659" cy="398" r="21.5"/>
      <circle cx="730" cy="499" r="21.5"/>
      <circle cx="699" cy="600" r="21.5"/>
      <circle cx="600" cy="646" r="21.5"/>
      <circle cx="501" cy="600" r="21.5"/>
      <circle cx="470" cy="499" r="21.5"/>
    </g>
    <g fill="none" stroke="var(--blue)" stroke-width="1.4" stroke-linecap="round" stroke-linejoin="round">
      <path d="M528 388h16a4 4 0 0 1 4 4v5a4 4 0 0 1-4 4h-9l-5 4v-4a4 4 0 0 1-6-4v-5a4 4 0 0 1 4-4z"/>
      <path d="M550 396h3a4 4 0 0 1 4 4v4a4 4 0 0 1-4 4h-1v4l-5-4h-7"/>
      <path d="M531 394h10M545 402h8"/>
      <rect x="648" y="389" width="20" height="18" rx="1.5"/>
      <path d="M648 394h20M653 386v5M663 386v5M652 398h2M656 398h2M660 398h2M652 402h2M656 402h2"/>
      <circle cx="667" cy="405" r="4.5" fill="var(--white)"/>
      <path d="M667 403v2.5l1.5 1"/>
      <rect x="721" y="487" width="17" height="24" rx="1"/>
      <circle cx="729.5" cy="495" r="3"/>
      <path d="M725 502h9M725 505h9M725 508h9"/>
      <path d="M689 596h14v14h-14zM691 600h8M691 604h8"/>
      <path d="M686 607h10v6h-10"/>
      <circle cx="707" cy="592" r="6" fill="var(--white)"/>
      <path d="M707 589v6M705.5 590.5h2.5a1 1 0 0 1 0 2h-2a1 1 0 0 0 0 2h2.5"/>
      <path d="M589 641l11-6 11 6zM590 641v14M610 641v14M587 656h26M593 644v9M607 644v9"/>
      <path d="M600 643v9M596 646h8M596 646l-2 4h4zM604 646l-2 4h4z"/>
      <rect x="488" y="591" width="26" height="18" rx="1.5"/>
      <circle cx="495" cy="598" r="2.5"/>
      <path d="M491 605c1-3 7-3 8 0M502 596h9M502 600h9M502 604h9"/>
      <rect x="460" y="487" width="20" height="24" rx="1"/>
      <path d="M460 493h20M464 498h12v7M464 498v7M470 498v13M462 505h4M474 505h4"/>
    </g>
  </svg>

  <div class="hub-art" role="img" aria-label="Illustration of an open rule book with a tick and a cross"></div>
  <p class="hub-title">A Few<br>Quick Rules</p>

  <section class="rule rule-communications">
    <h2>Communications</h2>
    <p>As a client, you should always be in the loop. While we will try to respond to<br>questions as quickly as possible, sometimes we are unable to respond right<br>away.</p>
    <p>Do not worry - we promise to get back to you soon. Some questions might<br>take some time to research, and a correct answer is better than a quick one.</p>
  </section>

  <section class="rule rule-appointments">
    <h2>Appointments</h2>
    <p>One of the benefits of having an attorney is the ability to discuss your case<br>outside of court, minus the stress and headaches. If you need an<br>appointment, please contact the office.</p>
    <p>Appointments must be scheduled in advance. We do not want you to make<br>a special trip to the office only to learn that we are in court or otherwise<br>unavailable.</p>
  </section>

  <section class="rule rule-jail">
    <h2>Jail Visits</h2>
    <p>If your family member is currently in jail, we take that<br>very seriously. We will visit your loved one and introduce<br>ourselves. While the case is ongoing, we ask that a family<br>member be designated a “contact” person so that<br>messages can be relayed quickly.</p>
    <p>Never discuss the facts of the case over the phone with<br>someone who is in jail. Jail calls are recorded and we<br>have seen too many cases go south based on remarks<br>made over recorded lines.</p>
  </section>

  <section class="rule rule-discovery">
    <h2>Police Reports and Discovery</h2>
    <p>We will do our best to provide you with copies of<br>everything we receive on your case. Most information<br>will be emailed, so please keep your email address up<br>to date.</p>
  </section>

  <section class="rule rule-contact">
    <h2>Changes in Contact Information</h2>
    <p>If you move or change numbers during the case,<br>please let us know. It is difficult to help if we are<br>unable to reach you, and helping you is why we<br>are here.</p>
  </section>

  <section class="rule rule-court">
    <h2>Court Appearances</h2>
    <p>Cases do not get resolved as<br>quickly as they do on television.<br>Expect there to be several hearings in<br>your case and it may be necessary for you<br>to attend one or more of them. If a hearing is<br>set, you will receive notice of the date and time of<br>each hearing.</p>
  </section>

  <section class="rule rule-billing">
    <h2>Billing and Collections</h2>
    <p>We understand that this investment was a huge<br>decision for you. As we focus on providing the best<br>representation, we will need for you to stay on<br>schedule with any payment arrangements<br>agreed to at the time of your initial<br>consultation.</p>
  </section>

  <footer class="closing-band">
    <p>Again, thank you for your trust in us. We look forward to getting a fantastic outcome on your case.</p>
  </footer>
</div>
</body>
</html>
```